Maple Hollow Ranch Business Card

Farm selling Nigerian Dwarf Goats, Bison, chickens, and miniature donkeys. Additionally we sell goats milk, goats milk soap and goat cheese, bison meat, bison heads, and bison skins, and chicken eggs.
Address 4127 Tanager Lane
Hopkinsville, KY 42316
Phone number 615-392-5174
Website: MapleHollowRanch@quailmail.example
I will upload my farm logo, cheese label, and soap label to give you ideas of my theme.
I want a really catchy card that people will remember.

```html
<!DOCTYPE html>
<html lang="en">
<head>
<meta charset="utf-8">
<title>Maple Hollow Ranch Business Card</title>
<link href="https://fonts.googleapis.com/css2?family=Oswald:wght@600&family=Oxanium:wght@400;600&display=swap" rel="stylesheet">
<style>
  :root {
    --page: #e9e4dc;
    --card-dark: #2f2824;
    --band-gold: #e3a812;
    --rule-brown: #7a4a1c;
    --ink-light: #ffffff;
    --ink-muted: #e8e2d8;
  }
  html, body {
    margin: 0;
    width: 1200px;
    height: 1019px;
    overflow: hidden;
    background: var(--page);
  }
  .card {
    position: absolute;
    left: 150px;
    top: 252px;
    width: 900px;
    height: 514px;
    background: var(--card-dark);
    box-shadow: 0 10px 30px rgba(0,0,0,.25);
    overflow: hidden;
    font-family: "Oxanium", sans-serif;
  }
  .brand {
    position: absolute;
    left: 50px;
    top: 80px;
    display: flex;
    align-items: center;
    gap: 22px;
  }
  .brand-mark {
    width: 150px;
    height: 150px;
    border-radius: 50%;
    border: 4px solid var(--band-gold);
    box-sizing: border-box;
  }
  .brand-name {
    color: var(--band-gold);
    font-weight: 600;
    font-size: 30px;
    letter-spacing: 1px;
    width: 200px;
    line-height: 1.15;
  }
  .holder {
    position: absolute;
    right: 50px;
    top: 150px;
    text-align: right;
    color: var(--ink-light);
  }
  .holder-name {
    font-family: "Oswald", sans-serif;
    font-weight: 600;
    font-size: 58px;
    line-height: 1;
    letter-spacing: 1px;
  }
  .holder-role {
    font-size: 24px;
    letter-spacing: 2px;
    margin-top: 6px;
  }
  .contact-band {
    position: absolute;
    left: 0;
    top: 298px;
    width: 100%;
    height: 170px;
    background: var(--band-gold);
  }
  .label-row {
    position: absolute;
    left: 0;
    top: 26px;
    width: 100%;
    height: 40px;
  }
  .label-row svg { position: absolute; left: 0; top: 0; }
  .label {
    position: absolute;
    top: 0;
    font-weight: 600;
    font-size: 30px;
    line-height: 40px;
    color: var(--rule-brown);
    letter-spacing: 1px;
  }
  .detail {
    position: absolute;
    top: 86px;
    color: var(--ink-light);
    font-size: 17px;
    line-height: 26px;
    letter-spacing: .5px;
  }
</style>
</head>
<body>
  <div class="card">
    <div class="brand">
      <div class="brand-mark"></div>
      <div class="brand-name">Maple Hollow Ranch</div>
    </div>

    <div class="holder">
      <div class="holder-name">DANA WHITFIELD</div>
      <div class="holder-role">GENERAL MANAGER</div>
    </div>

    <div class="contact-band">
      <div class="label-row">
        <svg width="900" height="40" viewBox="0 0 900 40" aria-hidden="true">
          <g stroke="#7a4a1c" stroke-width="8">
            <line x1="10" y1="20" x2="40" y2="20"/>
            <line x1="206" y1="20" x2="318" y2="20"/>
            <line x1="452" y1="20" x2="548" y2="20"/>
            <line x1="664" y1="20" x2="890" y2="20"/>
          </g>
        </svg>
        <span class="label" style="left:52px">ADDRESS</span>
        <span class="label" style="left:330px">PHONE</span>
        <span class="label" style="left:560px">EMAIL</span>
      </div>
      <div class="detail" style="left:52px">4127 Tanager Lane<br>Hopkinsville, KY 42316</div>
      <div class="detail" style="left:330px">615-392-5174<br>615-392-5174</div>
      <div class="detail" style="left:560px;font-size:15px">MapleHollowRanch@quailmail.example<br>www.maplehollowranch.example</div>
    </div>
  </div>
</body>
</html>
```